Company or website name
- www.keyzUPdone.com
- Links to the website
- keyzupdone.com
- Describe your company and organization and target audience
- My name is dwight pelham from houston texas. I am a realtor. I have been trying very hard to develop a site that not only reflects me but can generate some business. I have a site with an idx search but it is too expensive and I really dont think IDX is the way to go. I just want a site that is neat and holds people interest. For this contest, I pretty much did all the work. I need your creativity. I have a file crate link that has everything in it. Each section is marked. I have about me, about what I do, How i am different, Neighborhoods i specialize in etc.
- The design should have the following
- I want in my site the following: I would Live Feed of my Snapvane and Friendloop page on the first main page I want my video playing as the main shot. I have 2 give a ways (something of value), buyers handbook and sellers handbook I do a monthly newsletter i would also like to give some attention to. I want a chat box that is either a bot or goes into text message to me www.keyzUPdone.com is the website url filecratr link: https://www.filecratr.net/sh/9kqpz27xw4ab51/BBTrq_7LmQ2hzxvNcPwYdKeRt?dl=0 If you can use the idx's that my assocation provides that would be great. I have been told they are frames, it is ok if you dont but if you can they do have some great info.

```html
<!DOCTYPE html>
<html lang="en">
<head>
<meta charset="utf-8">
<title>Realtor Home</title>
<link href="https://fonts.googleapis.com/css2?family=Montserrat:wght@400;500;700&display=swap" rel="stylesheet">
<style>
:root{
  --white:#ffffff;
  --ink:#111111;
  --gold:#f2c80f;
  --lime:#d9ef5a;
  --navy:#22213f;
  --hero-top:#3a3f68;
  --hero-mid:#4b5570;
  --hero-low:#3e5a3a;
  --sky:#8cbcf2;
  --lawn:#5a8f2e;
  --panel:rgba(255,255,255,0.55);
}
*{margin:0;padding:0;box-sizing:border-box}
html,body{width:1200px;height:2618px;overflow:hidden}
body{font-family:'Montserrat',sans-serif;background:var(--white);color:var(--ink);position:relative}
.hero{position:absolute;left:0;top:0;width:1200px;height:681px;
  background:linear-gradient(180deg,var(--hero-top) 0%,var(--hero-mid) 45%,#566a5c 70%,var(--hero-low) 100%);color:var(--white)}
.logo{position:absolute;left:59px;top:34px;font-size:31px;font-weight:700;letter-spacing:1px}
.nav{position:absolute;top:42px;font-size:21px;font-weight:400}
.social{position:absolute;right:30px;top:50px;display:flex;align-items:center;gap:14px;font-size:13px;font-weight:500;white-space:nowrap}
.social span{display:flex;align-items:center;gap:5px}
.social i{display:inline-block;width:12px;height:12px;background:var(--gold);border-radius:2px}
.hero-title{position:absolute;left:268px;top:188px;font-size:55px;font-weight:700;line-height:58px;white-space:nowrap}
.hero-title .accent{color:var(--gold)}
.hero-sub{position:absolute;left:260px;top:322px;width:650px;text-align:center;font-size:20px;line-height:25px}
.play{position:absolute;left:555px;top:396px}
.about-photo{position:absolute;left:0;top:681px;width:618px;height:672px;
  background:linear-gradient(180deg,var(--sky) 0%,#a9c7e3 30%,#8a6a58 55%,#6d7b45 72%,var(--lawn) 100%)}
.about-title{position:absolute;left:618px;width:582px;top:713px;text-align:center;font-size:54px;font-weight:500}
.about-text{position:absolute;left:727px;top:808px;width:398px;font-size:19px;line-height:33.5px}
.about-text p{margin-bottom:10px}
.btn-fill{position:absolute;left:773px;top:1250px;width:310px;height:74px;
  background:linear-gradient(90deg,var(--gold),var(--lime));display:flex;align-items:center;justify-content:center;font-size:21px;font-weight:500}
.services{position:absolute;left:0;top:1353px;width:1200px;height:566px;
  background:linear-gradient(90deg,#3f4e2a 0%,#8ea37a 20%,#c9d4c2 50%,#8ea37a 80%,#3f4e2a 100%)}
.service{position:absolute;top:0;width:484px;height:566px;background:var(--panel);text-align:center}
.service h2{margin-top:76px;font-size:29px;font-weight:700}
.service p{margin:42px auto 0;width:400px;font-size:21px;line-height:33.5px}
.btn-line{position:absolute;left:135px;top:459px;width:206px;height:65px;border:1.5px solid var(--ink);
  display:flex;align-items:center;justify-content:center;font-size:21px}
.contact{position:absolute;left:0;top:1919px;width:1200px;height:699px;background:var(--navy);color:var(--white)}
.portrait{position:absolute;left:152px;top:111px;width:187px;height:169px;background:linear-gradient(180deg,#8a8a8a,#3a3a3a)}
.agent-name{position:absolute;left:153px;top:312px;font-size:30px;font-weight:700}
.agent-bio{position:absolute;left:148px;top:354px;width:390px;font-size:21px;line-height:33.5px}
.field{position:absolute;left:660px;width:402px;border:1px solid var(--white);font-size:21px}
.field.email{top:143px;height:67px;padding:20px 30px}
.field.message{top:246px;height:241px;padding:14px 25px}
.btn-contact{position:absolute;left:660px;top:523px;width:291px;height:68px;border:2px solid var(--gold);
  display:flex;align-items:center;justify-content:center;font-size:21px}
</style>
</head>
<body>
<header class="hero" role="img" aria-label="Photo of a large suburban house with trees and a dark SUV in the driveway">
  <div class="logo">LOGO</div>
  <span class="nav" style="left:268px">Home</span>
  <span class="nav" style="left:392px">About</span>
  <span class="nav" style="left:517px;top:44px">Services</span>
  <span class="nav" style="left:680px">Contact</span>
  <div class="social"><span><i></i>Snapvane</span><span><i></i>Friendloop</span></div>
  <h1 class="hero-title">Our <span class="accent">Value</span> Proposition is<br>Accracy and Convenience</h1>
  <p class="hero-sub">Lorem ipsum dolor sit amet, consectetur adipiscing elit.<br>Egestas adipiscing&nbsp; enim posuere. Tellus cras</p>
  <svg class="play" width="63" height="63" viewBox="0 0 63 63"><circle cx="31.5" cy="31.5" r="31.5" fill="#e2b90c"/><path d="M24 18 L46 31.5 L24 45 Z" fill="#fff"/></svg>
</header>

<section>
  <div class="about-photo" role="img" aria-label="Photo of a brick two-storey house with a green lawn and brick path"></div>
  <h2 class="about-title">About Us</h2>
  <div class="about-text">
    <p>Lorem ipsum dolor sit amet, consectetur adipiscing elit. Consectetur mauris odio lobortis mauris aliquet sit. Tincidunt lorem malesuada non vulputate netus a id nunc mauris. Varius mattis sollicitudin orci, tortor. Consequat, vel molestie quam ullamcorper proin ornare lorem cras.</p>
    <p>Lorem ipsum dolor sit amet, consectetur adipiscing elit. Consectetur mauris odio lobortis mauris aliquet sit.</p>
  </div>
  <div class="btn-fill">Learn More</div>
</section>

<section class="services" role="img" aria-label="Photo of a white colonial house framed by trees">
  <div class="service" style="left:100px">
    <h2>What I Do</h2>
    <p>Lorem ipsum dolor sit amet, consectetur adipiscing elit. Congue eget facilisis volutpat malesuada elementum vel sit imperdiet eleifend. Eu, sed vel consequat imperdiet est nibh condimentum nibh a. Sed viverra aenean pharetra interdum scelerisque nam.</p>
    <div class="btn-line">Learn More</div>
  </div>
  <div class="service" style="left:623px">
    <h2>How I am Diffrents</h2>
    <p>Lorem ipsum dolor sit amet, consectetur adipiscing elit. Congue eget facilisis volutpat malesuada elementum vel sit imperdiet eleifend. Eu, sed vel consequat imperdiet est nibh condimentum nibh a. Sed viverra aenean pharetra interdum scelerisque nam.</p>
    <div class="btn-line" style="left:140px">Learn More</div>
  </div>
</section>

<section class="contact">
  <div class="portrait" role="img" aria-label="Portrait photo of the realtor"></div>
  <h3 class="agent-name">Dwight Pelham</h3>
  <p class="agent-bio">Lorem ipsum dolor sit amet, consectetur adipiscing elit. Congue eget facilisis volutpat malesuada elementum vel sit imperdiet eleifend. Eu, sed vel consequat imperdiet est nibh condimentum nibh a. Sed viverra aenean pharetra interdum scelerisque nam.</p>
  <div class="field email">Email</div>
  <div class="field message">Message</div>
  <div class="btn-contact">Contact Us</div>
</section>
</body>
</html>
```